WordPress Design (redesign) and Coding for Funeral Consulting Services & mobile app

I need an attractive SEO friendly WordPress design.

Incorporating all of the latest design standards in a graceful and appealing way. I'd like to see CTA's for for funeral consulting services. People should be able to purchase my consulting services directly from the website so I'd like to see nice buttons.

Funeral Consulting Services are the main topic for this website.

I also have an iOS app called Velomarque in the iOS Appvault Shelf. I want buttons and CTAs so that users can download the app right to their iOS device(s). Make this a secondary focus.

I want more of a mobile focus as that is where I expect the most traffic. Mobile users like to act quickly and they also like to scroll if their interest is captured so I want the design to reflect that.

End to end design
Large Creative Typography for increased mobile searchers.
attractive CTA’s
RGB Vivid / Bright Colors that match our logo
A menu that is easy to find and use on mobile devices
button(s) for iOS app download.

the current website is www.velomarque-example.com This website was a placeholder.
Updates

I'd need users to fill out a survey so that I may collect information from them to better provide service to them.

reference websites: Quillvant.com & Torbex.com for website design inspiratioin. reference Harnwick.com for blog

Target Market(s)

18-35 year old mobile users

Industry/Entity Type

Consulting

Coding

Coded - Design and coding required

Font styles to use
Sans Serif

Colors
fbee3d
000000
ffffff
cbcbcb
fefdec

Requirements
Must have
• iOS app logo and iOS app logo colors should have its own area/page
• CTA's for consulting services and app download. Main topic
• reviews (testimonials)
• Video area
• end to end design
• creative typography
Nice to have
• a beautiful blog page that blends well with the design
Should not have
• Any imagery related to funerals or burials.

```html
<!DOCTYPE html>
<html lang="en">
<head>
<meta charset="utf-8">
<title>Velomarque – Funeral Consulting Services</title>
<link href="https://fonts.googleapis.com/css2?family=Roboto:ital,wght@0,300;0,400;0,500;0,700;1,400&display=swap" rel="stylesheet">
<style>
:root{
  --yellow:#fbee3d;
  --yellow-soft:#f7f06a;
  --black:#000000;
  --white:#ffffff;
  --grey:#cbcbcb;
  --cream:#fefdec;
  --ink:#222222;
  --text:#3a3a3a;
  --muted:#8d8d8d;
  --panel:#ebebeb;
  --footer:#2b2b2b;
  --night:#1b191e;
}
*{box-sizing:border-box;margin:0;padding:0}
html,body{width:1200px;height:4235px;overflow:hidden}
body{font-family:"Roboto",Arial,sans-serif;color:var(--ink);background:var(--white);position:relative}
a{color:inherit;text-decoration:none}
section,header,footer{position:absolute;left:0;width:1200px;overflow:hidden}
.abs{position:absolute}
.btn{position:absolute;display:flex;align-items:center;justify-content:center;font-weight:500;font-size:14px;letter-spacing:.3px;text-transform:uppercase}

/* header */
.site-header{top:0;height:105px;background:var(--white)}
.brand{left:113px;top:28px;font-size:38px;font-weight:700;color:var(--black);letter-spacing:-.5px}
.main-nav{right:133px;top:40px;display:flex;gap:34px;font-size:17px;color:#555}
.main-nav .active{color:var(--black);font-weight:500;border-bottom:2px solid var(--yellow);padding-bottom:4px}

/* hero */
.hero{top:105px;height:587px;background:linear-gradient(100deg,#3b3336 0%,#5a4a4c 30%,#6f6e72 55%,#3a3b40 100%)}
.hero-photo{inset:0;background:linear-gradient(180deg,rgba(0,0,0,.1),rgba(0,0,0,.35))}
.hero-title{left:118px;top:195px;font-size:40px;font-weight:500;color:var(--white);line-height:46px;text-transform:uppercase}
.hero-dots{left:558px;top:460px;display:flex;gap:8px}
.hero-dots span{width:14px;height:14px;border-radius:50%;background:var(--white)}
.hero-dots span.current{background:transparent;border:2px solid var(--white)}
.hero-curve{left:0;bottom:0;width:1200px;height:140px}

/* intro */
.intro{top:692px;height:268px;background:var(--white)}
.intro p{position:absolute;left:160px;top:12px;width:880px;text-align:center;font-size:15.5px;line-height:29px;color:var(--text)}
.intro .btn{left:446px;top:169px;width:297px;height:45px;background:var(--black);color:var(--white);text-transform:none;font-size:16px}

/* split */
.split{top:960px;height:316px}
.split-dark{left:0;top:0;width:596px;height:316px;background:var(--black)}
.split-light{left:596px;top:0;width:604px;height:316px;background:var(--yellow)}
.split p{position:absolute;font-size:14.5px;line-height:24px;text-align:center}
.split-dark p{left:150px;top:100px;width:300px;color:var(--white)}
.split-light p{left:86px;top:66px;width:420px;color:var(--black)}
.split-dark .btn{left:246px;top:217px;width:209px;height:45px;border:2px solid var(--yellow);color:var(--yellow)}
.split-light .btn{left:146px;top:217px;width:209px;height:45px;border:2px solid var(--black);color:var(--black)}

/* friend */
.friend{top:1276px;height:466px;background:var(--grey)}
.friend-ring{left:115px;top:46px;width:362px;height:362px;border-radius:50%;border:2px solid #555;background:var(--white);padding:6px}
.friend-photo{width:100%;height:100%;border-radius:50%;background:linear-gradient(135deg,#b9aba4,#7d6c66 55%,#4e4644)}
.friend h2{left:537px;top:86px;width:520px;font-size:19px;font-weight:400;line-height:26px;color:var(--black)}
.friend p{left:537px;top:155px;width:520px;font-size:14.5px;line-height:24px;color:var(--text)}
.friend .btn{left:531px;top:350px;width:183px;height:45px;background:var(--yellow);color:var(--black);font-size:13.5px}

/* survey */
.survey{top:1742px;height:305px;background:linear-gradient(90deg,#6b6b6b,#4e4e4e)}
.survey-photo{left:0;top:0;width:700px;height:305px;clip-path:polygon(0 0,78% 0,62% 100%,0 100%);background:linear-gradient(120deg,#f1f1f1,#cfc7c2 55%,#9a8f8a)}
.survey p{left:683px;top:65px;width:420px;font-size:15px;line-height:25px;color:var(--white)}
.survey .btn{left:689px;top:184px;width:161px;height:45px;background:var(--black);color:var(--white);font-size:13px}

/* video */
.video{top:2047px;height:437px;background:radial-gradient(circle at 45% 30%,#2d2a2c,var(--night) 70%)}
.video h2{left:124px;top:93px;font-size:28px;font-weight:400;color:var(--white)}
.video p{left:126px;top:145px;width:420px;font-size:13.5px;line-height:22px;color:#9a9a9a}
.video .btn{left:130px;top:297px;width:161px;height:45px;border:2px solid var(--yellow);color:var(--white);font-size:13px}
.video-frame{left:613px;top:71px;width:457px;height:276px;background:linear-gradient(120deg,#d9d5d2,#a89f9a 50%,#6e6560)}
.play{left:803px;top:171px;width:76px;height:76px}

/* app */
.app{top:2484px;height:404px;background:linear-gradient(90deg,var(--yellow) 0%,var(--yellow) 55%,var(--yellow-soft) 100%)}
.app h2{left:138px;top:115px;font-weight:400;color:var(--black);text-transform:uppercase}
.app .lead{font-size:26px;line-height:30px;display:block}
.app .strong{font-size:33px;line-height:38px;display:block}
.store-btn{left:141px;top:206px;width:147px;height:57px;border-radius:9px;background:var(--black);color:var(--white);display:flex;flex-direction:column;justify-content:center;padding-left:18px}
.store-btn small{font-size:10px}
.store-btn b{font-size:15px;font-weight:500}
.app-device{left:728px;top:0;width:280px;height:404px;border-radius:60px 60px 0 0;background:linear-gradient(160deg,#f4f4f4,#d8d2c8 60%,#c9a98d)}

/* blog */
.blog{top:2888px;height:536px;background:var(--panel)}
.section-title{position:absolute;left:0;width:1200px;text-align:center;font-size:28px;font-weight:400;color:var(--black)}
.blog .section-title{top:40px}
.post-lead{left:107px;top:90px;width:480px;height:390px;background:var(--yellow);box-shadow:0 1px 4px rgba(0,0,0,.15)}
.post-lead .thumb{left:0;top:0;width:480px;height:220px;background:linear-gradient(120deg,#cfc9c6,#8d817c 55%,#4d4543)}
.date{position:absolute;width:57px;height:70px;background:var(--black);color:var(--white);text-align:center;font-size:22px;font-weight:500;padding-top:10px;line-height:24px}
.date small{display:block;font-size:12px;line-height:16px}
.post-lead .date{left:0;top:150px}
.post-lead h3{left:30px;top:240px;width:420px;text-align:center;font-size:16.5px;font-weight:500;line-height:23px;color:var(--black)}
.post-lead p{left:40px;top:300px;width:400px;text-align:center;font-size:12px;line-height:17px;color:#333}
.read{position:absolute;font-size:12px;font-weight:500;color:var(--black)}
.post-lead .read{left:0;width:480px;text-align:center;top:350px}
.post-card{left:607px;width:480px;height:184px;background:var(--white);box-shadow:0 1px 4px rgba(0,0,0,.15)}
.post-card .thumb{left:0;top:0;width:212px;height:184px;background:linear-gradient(120deg,#dedad6,#a89a93 55%,#6d625e)}
.post-card .date{left:0;top:114px}
.post-card h3{left:232px;top:28px;width:230px;text-align:center;font-size:15px;font-weight:400;color:var(--black)}
.post-card p{left:242px;top:58px;width:210px;text-align:center;font-size:11px;line-height:15px;color:#444}
.post-card .read{left:232px;width:230px;text-align:center;top:122px}

/* testimonials */
.reviews{top:3424px;height:429px;background:var(--white)}
.reviews .section-title{top:54px}
.review{width:290px}
.review-box{position:absolute;left:0;top:0;width:290px;height:120px;background:var(--white);border-radius:6px;box-shadow:0 2px 8px rgba(0,0,0,.18)}
.review-box .quote{position:absolute;left:14px;top:14px;width:24px;height:20px}
.review-box p{position:absolute;left:48px;top:16px;width:220px;font-size:11px;line-height:17px;font-style:italic;color:#777}
.stars{position:absolute;left:48px;top:91px;display:flex;gap:4px}
.stars svg{width:15px;height:15px}
.avatar{position:absolute;left:6px;top:206px;width:52px;height:52px;border-radius:50%;background:linear-gradient(135deg,#c9c2bd,#7b706b)}
.author{position:absolute;left:72px;top:212px;font-size:13px;font-weight:500;color:var(--black)}
.author small{display:block;font-weight:400;font-size:11px;color:var(--muted);margin-top:6px}

/* footer */
.site-footer{top:3853px;height:382px;background:var(--footer);color:var(--white)}
.site-footer h4{position:absolute;top:71px;font-size:15px;font-weight:400;letter-spacing:.5px;text-transform:uppercase}
.links{position:absolute;top:108px;list-style:none;font-size:13px;line-height:28px;color:#d8d8d8}
.contact-list{position:absolute;left:534px;top:104px;list-style:none;font-size:12px;line-height:16px;color:#d8d8d8}
.contact-list li{display:flex;gap:10px;margin-bottom:10px}
.contact-list svg{width:14px;height:14px;flex:none;margin-top:1px}
.socials{position:absolute;left:534px;top:216px;display:flex;gap:14px}
.socials span{width:34px;height:34px;border-radius:50%;background:var(--white)}
.email-field{left:830px;top:97px;width:257px;height:36px;background:#454545;color:#cfcfcf;font-size:12px;display:flex;align-items:center;padding-left:12px}
.subscribe{left:830px;top:145px;width:144px;height:36px;background:var(--yellow);color:var(--black);text-transform:none;font-size:15px}
.rule{left:147px;top:311px;width:940px;height:1px;background:#4a4a4a}
.copyright{left:0;top:339px;width:1200px;text-align:center;font-size:11px;color:#8a8a8a}
</style>
</head>
<body>

<header class="site-header">
  <a class="brand abs" href="#">Velomarque</a>
  <nav class="main-nav abs">
    <a class="active" href="#">Home</a>
    <a href="#">About Us</a>
    <a href="#">Our App</a>
    <a href="#">Blogs</a>
    <a href="#">Video</a>
    <a href="#">Review</a>
    <a href="#">Contact Us</a>
  </nav>
</header>

<section class="hero">
  <div class="hero-photo abs" role="img" aria-label="Photo of a consultant talking with a client"></div>
  <h1 class="hero-title abs">We provide funeral<br>consulting services</h1>
  <div class="hero-dots abs"><span class="current"></span><span></span><span></span><span></span></div>
  <svg class="hero-curve abs" viewBox="0 0 1200 140" preserveAspectRatio="none">
    <path d="M330 82 C600 22 880 10 1150 38" fill="none" stroke="#fbee3d" stroke-width="10"/>
    <path d="M0 140 L0 128 C380 50 800 22 1200 48 L1200 140 Z" fill="#ffffff"/>
  </svg>
</section>

<section class="intro">
  <p>Funerals are expensive. Having to finance one suddenly can be a burden to many families, especially those that are uninsured or unprepared. Not coincidently, there is often a windfall of money at this time, in the form of donations, family contributions, and life insurance proceeds. Families tend to consider that money ‘going away’ funds. The funeral industry wants to pressure you into spending your last dollar on that event</p>
  <a class="btn" href="#">DON’T Throw Money Away</a>
</section>

<section class="split">
  <div class="split-dark abs">
    <p>The fact is, life insurance was never intended to be fully used on a fancy funeral, but rather as a hedge against disaster for the survivors.</p>
    <a class="btn" href="#">Save Money</a>
  </div>
  <div class="split-light abs">
    <p>A funeral consultant is someone who, on their own, goes out and does all the things related to making funeral arrangements. However we do so with your budget and your ideals in mind. We represent you as your spokesperson and friend during this tough time.</p>
    <a class="btn" href="#">Get Help ASAP</a>
  </div>
</section>

<section class="friend">
  <div class="friend-ring abs"><div class="friend-photo" role="img" aria-label="Photo of two friends sitting together, one comforting the other"></div></div>
  <h2 class="abs">The first step in funeral planning, particularly if you find yourself at-need, is to get a friend by your side.</h2>
  <p class="abs">This should be someone who is somewhat removed from the deceased, so the friend’s emotions will not be a factor. It should also be someone whose judgement you trust and, preferably, someone who has been through the arrangement process in the recent past. This friend should be someone who has the strength of character to say ‘NO’ or at least ‘Not YET’, to keep you from being pressured into hasty, expensive financial decisions.</p>
  <a class="btn" href="#">Save Money Today</a>
</section>

<section class="survey">
  <div class="survey-photo abs" role="img" aria-label="Photo of a woman resting a reassuring hand on a friend’s shoulder"></div>
  <p class="abs">In a survey of several thousand funeral directors, in response to the question Why would you say funerals cost so much?, over 85% replied  Emotional overspending by the family.”</p>
  <a class="btn" href="#">Get Help Now</a>
</section>

<section class="video">
  <h2 class="abs">WATCH OUR VIDEO</h2>
  <p class="abs">Iaculis diam a nisi accumsan viverra duis sed tellus at tortor vestibulum gravida praesent elementum elit at tellus curabitur metus ipsum luctus eu malesuada ut tincidunt sed diam donec quis mi sed magna tincidunt accumsan suspendisse risus nibh ultricies eu</p>
  <a class="btn" href="#">View More</a>
  <div class="video-frame abs" role="img" aria-label="Video still of a young man looking thoughtful"></div>
  <svg class="play abs" viewBox="0 0 76 76"><circle cx="38" cy="38" r="38" fill="#ffffff"/><path d="M30 23 L54 38 L30 53 Z" fill="#000000"/></svg>
</section>

<section class="app">
  <h2 class="abs"><span class="lead">Want to download</span><span class="strong">Velomarque app now</span></h2>
  <a class="store-btn abs" href="#"><small>Download on the</small><b>Appvault Shelf</b></a>
  <div class="app-device abs" role="img" aria-label="Hand holding a phone showing the Velomarque app start screen"></div>
</section>

<section class="blog">
  <h2 class="section-title">LATEST BLOGS</h2>
  <article class="post-lead abs">
    <div class="thumb abs" role="img" aria-label="Photo of a man supporting a grieving friend"></div>
    <div class="date">10<small>DEC</small></div>
    <h3 class="abs">Morbi diam mauris viverra in gravida eu mattis in ante eget arcu Morbi porta libero</h3>
    <p class="abs">Aliquam curabitur iaculis tempus eros curabitur vel mi sit amet magna malesuada ultrices ut mi erat</p>
    <a class="read" href="#">READ MORE</a>
  </article>
  <article class="post-card abs" style="top:90px">
    <div class="thumb abs" role="img" aria-label="Photo of a person writing at a desk"></div>
    <div class="date">04<small>DEC</small></div>
    <h3 class="abs">Eu mattis in ante eget arcu</h3>
    <p class="abs">Aliquam curabitur iaculis tempus eros curabitur vel mi sit amet magna malesuada ultrices ut mi erat</p>
    <a class="read" href="#">READ MORE</a>
  </article>
  <article class="post-card abs" style="top:302px">
    <div class="thumb abs" role="img" aria-label="Photo of a man sitting deep in thought"></div>
    <div class="date">02<small>DEC</small></div>
    <h3 class="abs">Eu mattis in ante eget arcu</h3>
    <p class="abs">Aliquam curabitur iaculis tempus eros curabitur vel mi sit amet magna malesuada ultrices ut mi erat</p>
    <a class="read" href="#">READ MORE</a>
  </article>
</section>

<section class="reviews">
  <h2 class="section-title">TESTIMONIALS</h2>

  <div class="review abs" style="left:135px;top:113px">
    <div class="review-box">
      <svg class="quote" viewBox="0 0 24 20"><path d="M0 20V11C0 5 3 1 9 0l1 3C6 4 5 7 5 9h5v11zM14 20V11c0-6 3-10 9-11l1 3c-4 1-5 4-5 6h5v11z" fill="#555"/></svg>
      <p>Morbi diam mauris viverra in gravida eu mattis in ante Morbi eget arcu Morbi porta libero ut ullamcorper nonummy nibh</p>
      <div class="stars"><svg viewBox="0 0 20 20"><path d="M10 1l2.8 5.8 6.2.9-4.5 4.4 1.1 6.3L10 15.4 4.4 18.4l1.1-6.3L1 7.7l6.2-.9z" fill="#f2c21b"/></svg><svg viewBox="0 0 20 20"><path d="M10 1l2.8 5.8 6.2.9-4.5 4.4 1.1 6.3L10 15.4 4.4 18.4l1.1-6.3L1 7.7l6.2-.9z" fill="#f2c21b"/></svg><svg viewBox="0 0 20 20"><path d="M10 1l2.8 5.8 6.2.9-4.5 4.4 1.1 6.3L10 15.4 4.4 18.4l1.1-6.3L1 7.7l6.2-.9z" fill="#f2c21b"/></svg><svg viewBox="0 0 20 20"><path d="M10 1l2.8 5.8 6.2.9-4.5 4.4 1.1 6.3L10 15.4 4.4 18.4l1.1-6.3L1 7.7l6.2-.9z" fill="#f2c21b"/></svg></div>
    </div>
    <div class="avatar" role="img" aria-label="Reviewer portrait"></div>
    <div class="author">By Author Name<small>City Location</small></div>
  </div>

  <div class="review abs" style="left:466px;top:113px">
    <div class="review-box">
      <svg class="quote" viewBox="0 0 24 20"><path d="M0 20V11C0 5 3 1 9 0l1 3C6 4 5 7 5 9h5v11zM14 20V11c0-6 3-10 9-11l1 3c-4 1-5 4-5 6h5v11z" fill="#555"/></svg>
      <p>Morbi diam mauris viverra in gravida eu mattis in ante Morbi eget arcu Morbi porta libero ut ullamcorper nonummy nibh</p>
      <div class="stars"><svg viewBox="0 0 20 20"><path d="M10 1l2.8 5.8 6.2.9-4.5 4.4 1.1 6.3L10 15.4 4.4 18.4l1.1-6.3L1 7.7l6.2-.9z" fill="#f2c21b"/></svg><svg viewBox="0 0 20 20"><path d="M10 1l2.8 5.8 6.2.9-4.5 4.4 1.1 6.3L10 15.4 4.4 18.4l1.1-6.3L1 7.7l6.2-.9z" fill="#f2c21b"/></svg><svg viewBox="0 0 20 20"><path d="M10 1l2.8 5.8 6.2.9-4.5 4.4 1.1 6.3L10 15.4 4.4 18.4l1.1-6.3L1 7.7l6.2-.9z" fill="#f2c21b"/></svg><svg viewBox="0 0 20 20"><path d="M10 1l2.8 5.8 6.2.9-4.5 4.4 1.1 6.3L10 15.4 4.4 18.4l1.1-6.3L1 7.7l6.2-.9z" fill="#f2c21b"/></svg></div>
    </div>
    <div class="avatar" role="img" aria-label="Reviewer portrait"></div>
    <div class="author">By Author Name<small>City Location</small></div>
  </div>

  <div class="review abs" style="left:799px;top:113px">
    <div class="review-box">
      <svg class="quote" viewBox="0 0 24 20"><path d="M0 20V11C0 5 3 1 9 0l1 3C6 4 5 7 5 9h5v11zM14 20V11c0-6 3-10 9-11l1 3c-4 1-5 4-5 6h5v11z" fill="#555"/></svg>
      <p>Morbi diam mauris viverra in gravida eu mattis in ante Morbi eget arcu Morbi porta libero ut ullamcorper nonummy nibh</p>
      <div class="stars"><svg viewBox="0 0 20 20"><path d="M10 1l2.8 5.8 6.2.9-4.5 4.4 1.1 6.3L10 15.4 4.4 18.4l1.1-6.3L1 7.7l6.2-.9z" fill="#f2c21b"/></svg><svg viewBox="0 0 20 20"><path d="M10 1l2.8 5.8 6.2.9-4.5 4.4 1.1 6.3L10 15.4 4.4 18.4l1.1-6.3L1 7.7l6.2-.9z" fill="#f2c21b"/></svg><svg viewBox="0 0 20 20"><path d="M10 1l2.8 5.8 6.2.9-4.5 4.4 1.1 6.3L10 15.4 4.4 18.4l1.1-6.3L1 7.7l6.2-.9z" fill="#f2c21b"/></svg><svg viewBox="0 0 20 20"><path d="M10 1l2.8 5.8 6.2.9-4.5 4.4 1.1 6.3L10 15.4 4.4 18.4l1.1-6.3L1 7.7l6.2-.9z" fill="#f2c21b"/></svg></div>
    </div>
    <div class="avatar" role="img" aria-label="Reviewer portrait"></div>
    <div class="author">By Author Name<small>City Location</small></div>
  </div>
</section>

<footer class="site-footer">
  <h4 style="left:147px">Company</h4>
  <ul class="links" style="left:147px"><li>Home</li><li>About</li><li>Blog</li><li>Videos</li></ul>

  <h4 style="left:339px">Resources</h4>
  <ul class="links" style="left:339px"><li>Our App</li><li>Review</li><li>Get Help</li><li>Contact Us</li></ul>

  <h4 style="left:534px">Contact Us</h4>
  <ul class="contact-list">
    <li><svg viewBox="0 0 14 14"><path d="M7 0a5 5 0 0 0-5 5c0 3.5 5 9 5 9s5-5.5 5-9a5 5 0 0 0-5-5zm0 7a2 2 0 1 1 0-4 2 2 0 0 1 0 4z" fill="#fff"/></svg><span>18 Larkspur Row, Suite 4<br>Fenwick, OR 97000</span></li>
    <li><svg viewBox="0 0 14 14"><path d="M3 0l2.5 3-1.5 2c1 2 3 4 5 5l2-1.5 3 2.5-2 3C6 14 0 8 0 2z" fill="#fff"/></svg><span>(555) 014-2290</span></li>
    <li><svg viewBox="0 0 14 14"><rect x="0" y="2" width="14" height="10" fill="#fff"/><path d="M0 2l7 5 7-5" fill="none" stroke="#2b2b2b" stroke-width="1.3"/></svg><span>info@velomarque-example.com</span></li>
  </ul>
  <div class="socials"><span></span><span></span><span></span><span></span></div>

  <h4 style="left:830px">Sign Up Newsletter</h4>
  <div class="email-field abs">Email address</div>
  <a class="btn subscribe" href="#">Subscribe</a>

  <div class="rule abs"></div>
  <p class="copyright abs">© 2017 Company Name. All right reserved</p>
</footer>

</body>
</html>
```